Dermatologist office in Brasilia. My with "target customers" are specially women.

I’m a dermatologist who works since 2006 in Brasilia. In 2017 I decided to change and improve my career. I decided to work more with cosmetics (Lumiqa and fillers), I still work with clinical and surgical dermatology.
Most of my patients are women but 20-30% are children and men.
I would like to see designs that use a butterfly and the color aquamarine with details in gold.

Industry/Entity Type

Cosmetics

Font styles to use
Sans Serif

Colors
33b8a4
87cfc6
cfeae6
85cae6

Requirements
Must have
• My project must have my name (Harumi Okeda) and my medical specialty (Dermatologista)
Nice to have
• The colors I prefer are aquamarine or Corvell Jade Tin.
• I also prefer a butterfly that means transformation and a new life.
• I prefer a sofisticated and also minimalist design.

```html
<!DOCTYPE html>
<html lang="en">
<head>
<meta charset="utf-8">
<title>Harumi Okeda — Business Card</title>
<link href="https://fonts.googleapis.com/css2?family=Josefin+Sans:wght@300;400&family=Arimo:wght@400;700&display=swap" rel="stylesheet">
<style>
  :root {
    --backdrop: #2b2b2b;
    --card: #ffffff;
    --ink: #3a3a3a;
    --ink-soft: #5b5b5b;
    --aqua: #33b8a4;
    --aqua-mid: #87cfc6;
    --aqua-pale: #cfeae6;
    --sky: #85cae6;
  }
  * { margin: 0; padding: 0; box-sizing: border-box; }
  html, body { width: 1200px; height: 930px; overflow: hidden; background: var(--backdrop); }
  .canvas {
    width: 1200px; height: 930px;
    display: flex; flex-direction: column; align-items: center; justify-content: space-evenly;
  }
  .card {
    position: relative;
    width: 740px; height: 423px;
    background: var(--card);
    border-radius: 22px;
    overflow: hidden;
    box-shadow: 0 10px 30px rgba(0,0,0,.35);
  }

  /* Brand lockup */
  .brand { display: flex; flex-direction: column; align-items: center; font-family: "Josefin Sans", sans-serif; color: var(--ink); }
  .brand-dot { width: 44px; height: 44px; border-radius: 50%; background: var(--aqua); margin-bottom: 18px; }
  .brand-name { font-weight: 400; font-size: 30px; letter-spacing: 15px; padding-left: 15px; text-transform: uppercase; }
  .brand-role { font-weight: 300; font-size: 11px; letter-spacing: 7px; padding-left: 7px; margin-top: 8px; text-transform: uppercase; color: var(--ink); }

  .card-front { display: flex; align-items: center; justify-content: center; }

  /* Back */
  .card-back .brand { position: absolute; top: 40px; right: 46px; }
  .card-back .brand-dot { width: 30px; height: 30px; margin-bottom: 12px; }
  .card-back .brand-name { font-size: 19px; letter-spacing: 9px; padding-left: 9px; }
  .card-back .brand-role { font-size: 8px; letter-spacing: 5px; padding-left: 5px; margin-top: 6px; }

  .accent-bar { position: absolute; left: 0; top: 150px; width: 10px; height: 52px; border-left: 5px solid var(--aqua); border-right: 2px solid var(--aqua-mid); }
  .holder { position: absolute; left: 46px; top: 148px; font-family: "Arimo", sans-serif; }
  .holder-name { font-weight: 700; font-size: 29px; color: var(--ink-soft); letter-spacing: -0.5px; text-transform: uppercase; }
  .holder-role { font-size: 18px; color: var(--aqua); margin-top: 2px; }

  .contact { position: absolute; left: 60px; top: 272px; list-style: none; font-family: "Arimo", sans-serif; font-size: 19px; color: var(--ink-soft); line-height: 25px; }
  .contact li { display: flex; align-items: center; gap: 10px; }
  .contact svg { width: 13px; height: 13px; flex: none; }

  .address { position: absolute; right: 46px; top: 150px; font-family: "Arimo", sans-serif; font-size: 19px; line-height: 25px; color: var(--ink-soft); text-align: left; }

  .wave { position: absolute; left: 0; bottom: 0; width: 740px; height: 423px; }
</style>
</head>
<body>
<main class="canvas">

  <section class="card card-front" aria-label="Card front">
    <div class="brand">
      <span class="brand-dot"></span>
      <span class="brand-name">Harumi Okeda</span>
      <span class="brand-role">Dermatologist</span>
    </div>
  </section>

  <section class="card card-back" aria-label="Card back">
    <svg class="wave" viewBox="0 0 740 423" role="img" aria-label="Decorative teal wave band along the bottom edge">
      <defs>
        <linearGradient id="waveFill" x1="0" y1="1" x2="1" y2="0">
          <stop offset="0" stop-color="var(--aqua-pale)"/>
          <stop offset="1" stop-color="var(--aqua)"/>
        </linearGradient>
      </defs>
      <path d="M0,400 C200,420 400,385 540,300 C620,250 680,225 740,218 L740,423 L0,423 Z" fill="url(#waveFill)"/>
    </svg>

    <div class="brand">
      <span class="brand-dot"></span>
      <span class="brand-name">Harumi Okeda</span>
      <span class="brand-role">Dermatologist</span>
    </div>

    <span class="accent-bar"></span>
    <div class="holder">
      <p class="holder-name">Harumi Okeda</p>
      <p class="holder-role">Dermetologist</p>
    </div>

    <p class="address">418/B Willow Crest, Midtown,<br>Brookfield, USA</p>

    <ul class="contact">
      <li>
        <svg viewBox="0 0 16 16" aria-hidden="true"><path d="M3.5 1.5l2.5 0 1 3.5-1.8 1.2a9 9 0 0 0 4.6 4.6L11 9l3.5 1v2.5c0 1-1 2-2 2A11.5 11.5 0 0 1 1.5 3.5c0-1 1-2 2-2z" fill="var(--aqua)"/></svg>
        0457 296 318
      </li>
      <li>
        <svg viewBox="0 0 16 16" aria-hidden="true"><rect x="1.5" y="3.5" width="13" height="9" rx="1" fill="none" stroke="var(--aqua)" stroke-width="1.6"/><path d="M2 4.5l6 4.5 6-4.5" fill="none" stroke="var(--aqua)" stroke-width="1.6"/></svg>
        info@harumiokeda.com.au
      </li>
      <li>
        <svg viewBox="0 0 16 16" aria-hidden="true"><circle cx="8" cy="8" r="6.5" fill="none" stroke="var(--aqua)" stroke-width="1.5"/><ellipse cx="8" cy="8" rx="2.8" ry="6.5" fill="none" stroke="var(--aqua)" stroke-width="1.2"/><path d="M1.5 8h13" stroke="var(--aqua)" stroke-width="1.2"/></svg>
        www.harumiokeda.com.au
      </li>
    </ul>
  </section>

</main>
</body>
</html>
```